verdant terraces simple classy business card design

my name is colin barrow and I run a gardening business aimed at high class verdant terraces. the business name is verdant terraces and our logo was designed on pixel harbour .My clientel are anything from residential homes to businesses. I take pride in my work and know that I offer a service like no other in my area.
The business card will be used to represent my business and I want it to be not only rememberable, but simplistic and modern. Eye catching too. Of course I would like it relatable to gardening and appealing to the correct clientel - those being garden enthusiasts, prestigious homes and businesses that are after top of the line gardening services like no other on the market.
I am not a typical lawn mowing business so I don't want a typical card design that represents that. The gardens I work with are generally million dollar properties with owners who are very garden proud looking for upkeep and guidance from me along with sometimes whole new garden designs. I want the business cards to show to my clients that I take pride, as they do, in their garden. And I want them to know from my card that I am a professional, qualified horticulturist offering them a top of the line service for life. I want them to refer my business on. I want them to look at my business card and see class and professionalism in a modern unique bold way.
The card should be simple with the possibility of the logo on the front being embossed/debossed and my details on the back the card should have a organic garden feel it's very important to me that it is absolutely perfect
I am also very open to ideas and suggestions so look forward to seeing the designs. the business logo has been supplied with this project and I want the card to be double sided

Contact info is
Colin Barrow - Managing Director / Horticulturist
Phone : 0481 526 704
Email: colinbarrow@verdantterraces.example.au

Target Market(s)

high class gardens residential and commercial

Industry/Entity Type

Gardener

Contact Information for Business Card

Contact info is
Phone : 0481 526 704

PLEASE MAKE CARD DOUBLE SIDED

Requirements
Must have
• organic simple classy modern feel
• must flow with the current logo that has been supplied with this project
• Double sided
• Must explain in a simple way that I deal with high end gardens and I'm a qualified horticulturist
Nice to have
• embossed debossed logo
Should not have
• shouldn't be to busy or cheap looking

```html
<!DOCTYPE html>
<html lang="en">
<head>
<meta charset="utf-8">
<title>Verdant Terraces – Business Card</title>
<link rel="stylesheet" href="https://fonts.googleapis.com/css2?family=Montserrat:wght@400;600&display=swap">
<style>
  :root {
    --backdrop: #e8dccd;
    --card-white: #fbfbf9;
    --brand-green: #4e9a3d;
    --text-light: #f2f7ef;
    --rule-light: rgba(255, 255, 255, 0.55);
    --card-shadow: 0 6px 16px rgba(60, 45, 30, 0.22);
  }
  * { margin: 0; padding: 0; box-sizing: border-box; }
  html, body { width: 1200px; height: 794px; overflow: hidden; }
  body {
    background: var(--backdrop);
    font-family: "Montserrat", Arial, sans-serif;
    position: relative;
  }
  .card {
    position: absolute;
    width: 560px;
    height: 342px;
    box-shadow: var(--card-shadow);
  }
  .card-front {
    left: 230px;
    top: 40px;
    background: var(--card-white);
    display: flex;
    align-items: center;
    justify-content: center;
    gap: 16px;
  }
  .brand-dot {
    width: 22px;
    height: 22px;
    border-radius: 50%;
    background: var(--brand-green);
  }
  .brand-name {
    color: var(--brand-green);
    font-weight: 600;
    font-size: 30px;
    letter-spacing: 0.14em;
    text-transform: uppercase;
  }
  .card-back {
    left: 410px;
    top: 412px;
    background: var(--brand-green);
    color: var(--text-light);
    text-align: center;
  }
  .back-mark {
    position: absolute;
    left: 50%;
    top: 34px;
    width: 80px;
    height: 80px;
    margin-left: -40px;
    border-radius: 50%;
    background: var(--text-light);
  }
  .rule {
    position: absolute;
    left: 80px;
    right: 80px;
    height: 1px;
    background: linear-gradient(90deg, transparent, var(--rule-light), transparent);
  }
  .rule-top { top: 138px; }
  .rule-bottom { top: 292px; }
  .contact {
    position: absolute;
    left: 0;
    right: 0;
    top: 150px;
  }
  .person-name { font-weight: 600; font-size: 20px; margin-bottom: 6px; }
  .person-role { font-size: 15px; margin-bottom: 12px; }
  .person-lines { font-size: 13px; margin-bottom: 8px; }
  .person-lines b { font-weight: 600; margin-right: 2px; }
  .person-lines span + span { margin-left: 14px; }
  .web { font-size: 14px; font-weight: 600; letter-spacing: 0.18em; }
</style>
</head>
<body>
  <section class="card card-front" aria-label="Card front">
    <span class="brand-dot"></span>
    <span class="brand-name">Verdant Terraces</span>
  </section>

  <section class="card card-back" aria-label="Card back">
    <span class="back-mark" aria-hidden="true"></span>
    <span class="rule rule-top"></span>
    <div class="contact">
      <p class="person-name">Colin Barrow</p>
      <p class="person-role">Managing Director / Horticulturist</p>
      <p class="person-lines">
        <span><b>P:</b> 0481 526 704</span>
        <span><b>E:</b> colinbarrow@verdantterraces.example.au</span>
      </p>
      <p class="web">verdantterraces.example.au</p>
    </div>
    <span class="rule rule-bottom"></span>
  </section>
</body>
</html>
```